HOME PAGE AND AND SECONDARY DESIGN FOR INTERNAL PAGES

Construction company looking for an easy to navagate professional serious greyscale website with a good clean feel simple clean menu and responsive friendly design. Our main clientele is commercial properties business owners and investors of rental properties. This website is going to be static HTML5 and would need multiple sizing files for clean fast rendering. Clean and accurate design files a must so if your experienced awesome modern greyscale designer let's get started I need this done as soon as possible.

Industry/Entity Type

construction, electrical, plumbing, commercial build outs

Number of Pages Required

2 page

Font styles to use
Sans Serif

Colors

Designer to choose only greyscale colors for use in the design.

Requirements
Must have
• Main Menu... Home, Services, Projects, About our team

```html
<!DOCTYPE html>
<html lang="en">
<head>
<meta charset="utf-8">
<title>Ironline Builders — Commercial Construction</title>
<link href="https://fonts.googleapis.com/css2?family=Michroma&family=Saira:wght@400;500;600;700&display=swap" rel="stylesheet">
<style>
:root{
  --ink:#1e1e1e;
  --char:#2b2b2b;
  --slate:#4a4a4a;
  --steel:#5c5c5c;
  --ash:#707070;
  --mist:#a8a8a8;
  --fog:#e4e4e4;
  --paper:#f3f3f3;
  --white:#ffffff;
  --display:"Michroma", "Saira", sans-serif;
  --text:"Saira", Arial, sans-serif;
}
*{margin:0;padding:0;box-sizing:border-box}
html,body{width:1200px;height:5144px;overflow:hidden}
body{position:relative;background:var(--white);font-family:var(--text);color:var(--ink)}
.abs{position:absolute}
.display{font-family:var(--display);text-transform:uppercase;letter-spacing:1px}
.body-copy{font-size:13px;line-height:1.6;color:var(--ash)}
.btn{display:inline-block;font-family:var(--text);font-weight:700;font-size:13px;letter-spacing:1px;text-transform:uppercase;padding:10px 22px;color:var(--white);background:var(--slate)}
.photo{position:absolute}
.circle-btn{position:absolute;width:48px;height:48px;border-radius:50%;border:1.5px solid currentColor;display:flex;align-items:center;justify-content:center}

/* hero */
.hero{position:absolute;left:0;top:0;width:1200px;height:688px;background:linear-gradient(160deg,#3a3a3a 0%,#1c1c1c 45%,#4d4d4d 70%,#262626 100%)}
.topline{position:absolute;right:80px;top:6px;font-size:11px;color:var(--mist)}
.nav{position:absolute;left:0;top:22px;width:1200px;height:60px}
.brand-box{position:absolute;left:180px;top:0;width:240px;height:150px;background:var(--white);display:flex;flex-direction:column;align-items:center;justify-content:center;gap:8px}
.brand-mark{width:22px;height:22px;border-radius:50%;background:var(--char)}
.brand-name{font-family:var(--text);font-weight:700;font-size:20px;letter-spacing:2px;color:var(--char);text-transform:uppercase}
.menu{position:absolute;left:530px;top:20px;display:flex;gap:36px;list-style:none}
.menu a{color:var(--white);font-size:12px;font-weight:600;letter-spacing:1px;text-decoration:none;text-transform:uppercase}
.nav-contact{position:absolute;left:980px;top:8px;padding:12px 30px;background:var(--ash)}
.hero-title{position:absolute;left:0;top:352px;width:1200px;text-align:center;color:var(--white)}
.hero-title .small{font-size:30px;display:block;margin-bottom:14px}
.hero-title .large{font-size:52px;display:block}
.scroll-dot{position:absolute;left:586px;top:620px;width:28px;height:28px;border-radius:50%;border:1.5px solid var(--ash)}

/* about */
.about{position:absolute;left:0;top:688px;width:1200px;height:612px;background:var(--fog)}
.about-text{position:absolute;left:868px;top:200px;width:260px}
.about-text h2{font-size:38px;color:var(--char);margin-bottom:20px}
.about-text .btn{margin-top:24px}

/* services */
.section-title{font-size:40px;color:var(--char)}
.service-card{position:absolute;top:1412px;height:430px}
.service-card .caption{position:absolute;left:28px;bottom:34px;width:520px;color:var(--white)}
.service-card h3{font-size:24px;margin-bottom:10px}
.service-card p{font-size:12px;line-height:1.5;color:var(--fog)}

/* advantages */
.adv{position:absolute;top:2060px;width:220px}
.adv-icon{width:76px;height:76px;border-radius:50%;border:1.5px solid var(--mist);display:flex;align-items:center;justify-content:center;margin-bottom:30px}
.adv h4{font-size:15px;font-weight:700;color:var(--char);text-transform:uppercase;margin-bottom:14px;letter-spacing:.5px}
.adv h4 span{font-size:22px}
.adv-divider{position:absolute;top:2060px;width:1px;height:340px;background:var(--fog)}

/* testimonial */
.trust{position:absolute;left:0;top:2504px;width:1200px;height:544px;background:var(--ash)}
.trust-panel{position:absolute;left:420px;top:0;width:380px;height:544px;background:var(--steel)}
.trust-title{position:absolute;left:148px;top:136px;font-size:40px;line-height:1.3;color:var(--white)}
.quote{position:absolute;left:480px;top:356px;width:300px;font-size:13px;line-height:1.6;color:var(--fog)}
.quote-name{position:absolute;left:480px;top:496px;font-size:14px;font-weight:700;color:var(--white);text-transform:uppercase;letter-spacing:1px}
.quote-role{position:absolute;left:480px;top:516px;font-size:11px;color:var(--mist)}

/* projects */
.projects{position:absolute;left:0;top:3048px;width:1200px;height:1032px;background:var(--paper)}
.project{position:absolute;width:452px;height:300px;border:6px solid var(--white)}
.project .label{position:absolute;left:26px;bottom:24px;color:var(--white)}
.project h5{font-size:20px;font-weight:700;letter-spacing:1px}
.project .addr{font-size:11px;color:var(--fog);display:flex;align-items:center;gap:6px;margin-top:4px}

/* contact */
.contact{position:absolute;left:0;top:4080px;width:1200px;height:640px;background:var(--steel)}
.contact-title{position:absolute;left:148px;top:112px;font-size:34px;line-height:1.35;color:var(--white)}
.contact-intro{position:absolute;left:730px;top:112px;width:320px;font-size:13px;line-height:1.6;color:var(--fog)}
.field{position:absolute;height:46px;border-bottom:1px solid var(--mist);font-size:12px;color:var(--fog);display:flex;align-items:flex-start}
.consent{position:absolute;left:148px;top:576px;font-size:11px;color:var(--fog);display:flex;align-items:center;gap:8px}
.consent i{width:12px;height:12px;border:1px solid var(--fog);display:inline-block}
.send{position:absolute;left:930px;top:560px;background:var(--char)}

/* footer */
.footer{position:absolute;left:0;top:4720px;width:1200px;height:424px;background:var(--fog)}
.footer-box{position:absolute;left:148px;top:20px;width:900px;height:290px;background:linear-gradient(135deg,#343434,#1b1b1b)}
.footer-contacts{position:absolute;left:80px;top:54px;list-style:none;color:var(--fog);font-size:13px}
.footer-contacts li{display:flex;align-items:center;gap:12px;margin-bottom:22px}
.socials{display:flex;gap:14px;margin-left:28px}
.socials i{width:12px;height:12px;border-radius:50%;background:var(--mist);display:block}
.footer-brand{position:absolute;left:340px;top:96px;width:220px;height:100px;display:flex;flex-direction:column;align-items:center;justify-content:center;gap:8px}
.footer-brand .brand-name{color:var(--white)}
.footer-brand .brand-mark{background:var(--white)}
.copyright{position:absolute;left:148px;top:368px;font-size:11px;color:var(--ash)}
.privacy{position:absolute;right:148px;top:368px;font-size:11px;color:var(--ash)}
</style>
</head>
<body>

<header class="hero" role="img" aria-label="Low angle view of a glass and steel commercial building in greyscale">
  <div class="topline">office@ironlinebuilders.example &nbsp;|&nbsp; (555) 014-2290</div>
  <nav class="nav">
    <div class="brand-box"><span class="brand-mark"></span><span class="brand-name">Ironline</span></div>
    <ul class="menu">
      <li><a href="#">Home</a></li>
      <li><a href="#">Services</a></li>
      <li><a href="#">Projects</a></li>
      <li><a href="#">About our team</a></li>
    </ul>
    <a class="btn nav-contact" href="#">Contact</a>
  </nav>
  <h1 class="hero-title display"><span class="small">We build</span><span class="large">Commercial real estate</span></h1>
  <span class="scroll-dot"></span>
</header>

<section class="about">
  <div class="photo" role="img" aria-label="Two engineers in hard hats reviewing building plans on site" style="left:0;top:0;width:760px;height:612px;background:linear-gradient(120deg,#cfcfcf 0%,#9a9a9a 45%,#d8d8d8 100%)"></div>
  <div class="about-text">
    <h2 class="display">About us</h2>
    <p class="body-copy">We plan, build and finish commercial spaces with steady crews, clear schedules and honest pricing. From shell to final inspection, one team stays accountable for every detail on site.</p>
    <a class="btn" href="#">Read more</a>
  </div>
</section>

<h2 class="abs display section-title" style="left:148px;top:1320px">Our services</h2>
<span class="circle-btn" style="left:980px;top:1320px;color:var(--slate)"><svg width="16" height="10" viewBox="0 0 16 10"><path d="M15 5H2M6 1L2 5l4 4" fill="none" stroke="currentColor" stroke-width="1.5"/></svg></span>
<span class="circle-btn" style="left:1050px;top:1320px;color:var(--slate)"><svg width="16" height="10" viewBox="0 0 16 10"><path d="M1 5h13M10 1l4 4-4 4" fill="none" stroke="currentColor" stroke-width="1.5"/></svg></span>

<article class="service-card" style="left:148px;width:640px">
  <div class="photo" role="img" aria-label="Tower crane over a construction site at dusk" style="inset:0;background:linear-gradient(180deg,#6e6e6e 0%,#8c8c8c 40%,#2e2e2e 100%)"></div>
  <div class="caption"><h3 class="display">Construction</h3><p>Ground-up builds managed from permit to handover with one point of contact.</p></div>
</article>
<article class="service-card" style="left:840px;width:360px">
  <div class="photo" role="img" aria-label="Team meeting around a table in an office" style="inset:0;background:linear-gradient(180deg,#9a9a9a 0%,#5a5a5a 60%,#2b2b2b 100%)"></div>
  <div class="caption" style="width:330px"><h3 class="display">Commercial build</h3><p>Tenant build outs, electrical and plumbing for offices and retail.</p></div>
</article>

<h2 class="abs display section-title" style="left:0;top:1950px;width:1200px;text-align:center">Our advantages</h2>

<div class="adv" style="left:148px">
  <div class="adv-icon"><svg width="34" height="34" viewBox="0 0 34 34" fill="none" stroke="#2b2b2b" stroke-width="2"><circle cx="17" cy="17" r="13"/><circle cx="17" cy="17" r="7"/><circle cx="17" cy="17" r="2" fill="#2b2b2b"/></svg></div>
  <h4><span>#1</span> Customer focus</h4>
  <p class="body-copy">We listen first, then shape every plan around how your tenants, staff and customers will really use the finished space.</p>
</div>
<span class="adv-divider" style="left:396px"></span>
<div class="adv" style="left:420px">
  <div class="adv-icon"><svg width="34" height="34" viewBox="0 0 34 34" fill="none" stroke="#2b2b2b" stroke-width="2"><path d="M17 3l13 26H4z"/><circle cx="17" cy="20" r="3"/></svg></div>
  <h4><span>#2</span> Multi experience</h4>
  <p class="body-copy">Years of commercial work across electrical, plumbing and build outs mean fewer surprises and faster answers on site.</p>
</div>
<span class="adv-divider" style="left:660px"></span>
<div class="adv" style="left:684px">
  <div class="adv-icon"><svg width="34" height="34" viewBox="0 0 34 34" fill="none" stroke="#2b2b2b" stroke-width="2"><rect x="6" y="6" width="22" height="22"/><path d="M11 17l4 4 8-9"/></svg></div>
  <h4><span>#3</span> Professionalism</h4>
  <p class="body-copy">Clean job sites, licensed trades and written updates each week keep owners and investors informed from start to finish.</p>
</div>
<span class="adv-divider" style="left:924px"></span>
<div class="adv" style="left:948px">
  <div class="adv-icon"><svg width="34" height="34" viewBox="0 0 34 34" fill="none" stroke="#2b2b2b" stroke-width="2"><circle cx="17" cy="17" r="13"/><path d="M17 9v8l6 4"/></svg></div>
  <h4><span>#4</span> 24/7 support</h4>
  <p class="body-copy">Our service line stays open around the clock, so urgent repairs and questions never wait until Monday morning.</p>
</div>

<section class="trust">
  <div class="trust-panel"></div>
  <h2 class="trust-title display">Our<br>customers<br>trust us</h2>
  <span class="circle-btn" style="left:470px;top:276px;width:40px;height:40px;color:var(--white)"><svg width="14" height="10" viewBox="0 0 16 10"><path d="M15 5H2M6 1L2 5l4 4" fill="none" stroke="currentColor" stroke-width="1.5"/></svg></span>
  <span class="circle-btn" style="left:526px;top:276px;width:40px;height:40px;color:var(--white)"><svg width="14" height="10" viewBox="0 0 16 10"><path d="M1 5h13M10 1l4 4-4 4" fill="none" stroke="currentColor" stroke-width="1.5"/></svg></span>
  <p class="quote">“They delivered our retail build out on schedule and under budget. Communication was clear every week and the finished space looks sharp.”</p>
  <p class="quote-name">Dalton Reyes</p>
  <p class="quote-role">Property investor</p>
  <div class="photo" role="img" aria-label="Portrait of a smiling client in a suit seated at a desk" style="left:800px;top:0;width:400px;height:544px;background:linear-gradient(160deg,#e8e8e8 0%,#bdbdbd 55%,#6a6a6a 100%)"></div>
</section>

<section class="projects">
  <h2 class="abs display section-title" style="left:0;top:110px;width:1200px;text-align:center;line-height:1.35">We realize your<br>building project</h2>

  <article class="project" style="left:148px;top:252px">
    <div class="photo" role="img" aria-label="Glass office tower viewed from street level" style="inset:0;background:linear-gradient(180deg,#9d9d9d,#3c3c3c)"></div>
    <div class="label"><h5>LOREM IPSUM</h5><p class="addr"><svg width="9" height="12" viewBox="0 0 9 12"><path d="M4.5 0A4.5 4.5 0 0 0 0 4.5C0 8 4.5 12 4.5 12S9 8 9 4.5A4.5 4.5 0 0 0 4.5 0z" fill="#e4e4e4"/></svg>42 Granite Row, Millbrook 70412</p></div>
  </article>
  <article class="project" style="left:148px;top:552px">
    <div class="photo" role="img" aria-label="Concrete structure under construction with wet ground" style="inset:0;background:linear-gradient(180deg,#6b6b6b,#2a2a2a)"></div>
    <div class="label"><h5>LOREM IPSUM</h5><p class="addr"><svg width="9" height="12" viewBox="0 0 9 12"><path d="M4.5 0A4.5 4.5 0 0 0 0 4.5C0 8 4.5 12 4.5 12S9 8 9 4.5A4.5 4.5 0 0 0 4.5 0z" fill="#e4e4e4"/></svg>42 Granite Row, Millbrook 70412</p></div>
  </article>
  <article class="project" style="left:600px;top:212px">
    <div class="photo" role="img" aria-label="High-rise frame with cranes against a bright sky" style="inset:0;background:linear-gradient(180deg,#c9c9c9,#4a4a4a)"></div>
    <div class="label"><h5>LOREM IPSUM</h5><p class="addr"><svg width="9" height="12" viewBox="0 0 9 12"><path d="M4.5 0A4.5 4.5 0 0 0 0 4.5C0 8 4.5 12 4.5 12S9 8 9 4.5A4.5 4.5 0 0 0 4.5 0z" fill="#e4e4e4"/></svg>42 Granite Row, Millbrook 70412</p></div>
  </article>
  <article class="project" style="left:600px;top:512px">
    <div class="photo" role="img" aria-label="Timber roof framing seen from below" style="inset:0;background:linear-gradient(180deg,#8a8a8a,#333333)"></div>
    <div class="label"><h5>LOREM IPSUM</h5><p class="addr"><svg width="9" height="12" viewBox="0 0 9 12"><path d="M4.5 0A4.5 4.5 0 0 0 0 4.5C0 8 4.5 12 4.5 12S9 8 9 4.5A4.5 4.5 0 0 0 4.5 0z" fill="#e4e4e4"/></svg>42 Granite Row, Millbrook 70412</p></div>
  </article>

  <a class="btn abs" href="#" style="left:500px;top:900px;width:200px;text-align:center;background:var(--char)">View all projects</a>
</section>

<section class="contact">
  <h2 class="contact-title display">Contact us for<br>a quality<br>consultation</h2>
  <p class="contact-intro">Tell us about your property and timeline. Our estimators review every request and reply within one business day with next steps and a clear scope.</p>
  <div class="field" style="left:148px;top:330px;width:400px">Full name *</div>
  <div class="field" style="left:650px;top:330px;width:400px">Company name *</div>
  <div class="field" style="left:148px;top:420px;width:400px">Email address *</div>
  <div class="field" style="left:650px;top:420px;width:400px">Phone number *</div>
  <div class="field" style="left:148px;top:506px;width:902px;height:52px">Your message</div>
  <div class="consent"><i></i>I agree to the terms and privacy policy</div>
  <a class="btn send" href="#" style="padding:12px 30px">Send us</a>
</section>

<footer class="footer">
  <div class="footer-box" role="img" aria-label="Dark architectural photo of a building facade">
    <ul class="footer-contacts">
      <li><svg width="12" height="16" viewBox="0 0 9 12"><path d="M4.5 0A4.5 4.5 0 0 0 0 4.5C0 8 4.5 12 4.5 12S9 8 9 4.5A4.5 4.5 0 0 0 4.5 0z" fill="#e4e4e4"/></svg><span>2200 Quarry Park Rd, Suite 110<br>Millbrook 70412</span></li>
      <li><svg width="14" height="14" viewBox="0 0 14 14"><path d="M3 1l2 3-1.5 1.5a8 8 0 0 0 5 5L10 9l3 2-1 2.5C6 13 1 8 .5 2z" fill="#e4e4e4"/></svg>(555) 014-2290</li>
      <li><svg width="14" height="10" viewBox="0 0 14 10"><rect x=".5" y=".5" width="13" height="9" fill="none" stroke="#e4e4e4"/><path d="M.5.5L7 6 13.5.5" fill="none" stroke="#e4e4e4"/></svg>office@ironlinebuilders.example</li>
      <li class="socials"><i></i><i></i><i></i></li>
    </ul>
    <div class="footer-brand"><span class="brand-mark"></span><span class="brand-name">Ironline</span></div>
  </div>
  <p class="copyright">© Copyright 2024 Ironline Builders LLC | All Rights Reserved</p>
  <p class="privacy">Privacy Policy</p>
</footer>

</body>
</html>
```